Double-sided A5 leaflet with photos.

Design A5 leaflet double sided
With emphasis on we are cheaper than our competition as a hook
The colour can be whatever makes it look like a unique brand.
Try and use all the different photos because they are unique.
And put the different photos on there with headlines
Updates

Need extra days to review

Target Market(s)

The idea is it stands out people moving that you can offer different things to like taking their bed apart, taking their old furniture or they just want to move and want two men and the truck. Big or small or piano? Heavy furniture marble table? People who want their bed taken apart put back together again, piano moving, marble table. Moving fridge for washing machine. Moving small truck picture of big truck the poster is people walking past in the street. The pelmo leaflet is delivered to high rise unit blocks with 300 units.

Industry/Entity Type

Furniture removal

Colors
59FF00
82FF00
B8FF75
E3FFCB
F4FFEA

Requirements
Must have
• Try and use all the different photos the screenshot of the Varnex review next to the other photos we put beds together, etc
Nice to have
• It would be nice to have on one side all the different photos with headlines on each one saying what they do EG beds taken apart over the top of a photo .g

```html
<!DOCTYPE html>
<html lang="en">
<head>
<meta charset="utf-8">
<title>Steady Haulers – A5 Leaflet</title>
<link href="https://fonts.googleapis.com/css2?family=Alfa+Slab+One&family=Roboto:wght@400;700&display=swap" rel="stylesheet">
<style>
  :root{
    --bg:#d6d6d6;
    --green:#2f6b21;
    --green-dark:#234f18;
    --green-mid:#3d8129;
    --yellow:#ecf01c;
    --white:#ffffff;
    --ink:#1d1d1d;
    --line:#d9d9d9;
    --stamp:#ececec;
  }
  *{box-sizing:border-box;margin:0;padding:0}
  html,body{width:1200px;height:2660px;overflow:hidden;background:var(--bg);font-family:"Roboto",sans-serif}
  .leaflet{position:absolute;left:158px;width:884px;height:628px;overflow:hidden;background:var(--white)}
  .front{top:660px}
  .back{top:1372px}
  .slab{font-family:"Alfa Slab One",serif;text-transform:uppercase;line-height:1;white-space:nowrap}

  /* front */
  .front-green{position:absolute;left:0;top:0;width:884px;height:440px;background:linear-gradient(180deg,var(--green) 0%,var(--green-dark) 100%)}
  .hero-art{position:absolute;left:30px;top:58px;width:450px;height:420px;border-radius:50% 50% 40% 45%;background:radial-gradient(circle at 45% 45%,#e4e36a 0%,#6f9a3a 45%,#3a7a2a 75%,rgba(47,107,33,0) 100%)}
  .brand-badge{position:absolute;left:676px;top:20px;width:190px;height:190px;border-radius:50%;background:var(--white);display:flex;align-items:center;justify-content:center;text-align:center}
  .brand-badge span{font-family:"Alfa Slab One",serif;font-size:26px;color:var(--green);line-height:1.05}
  .headline{position:absolute;left:484px;top:222px}
  .headline .y{color:var(--yellow);font-size:45px;letter-spacing:1px;line-height:1.08}
  .headline .w{color:var(--white);font-size:66px;margin-top:2px}
  .phone-band{position:absolute;left:348px;top:420px;width:536px;height:52px;background:var(--yellow);clip-path:polygon(4% 0,100% 0,100% 100%,0 100%);display:flex;align-items:center;padding-left:30px;gap:12px;white-space:nowrap}
  .phone-band .num{font-family:"Alfa Slab One",serif;font-size:26px;color:var(--green)}
  .phone-band .sep{width:2px;height:30px;background:var(--green)}
  .phone-band .web{font-family:"Alfa Slab One",serif;font-size:12px;color:var(--green)}
  .offers{position:absolute;left:0;top:484px;width:884px;height:144px;display:flex;align-items:center;background:linear-gradient(180deg,#f7f7f7,#fff)}
  .offer{flex:1;display:flex;align-items:center;gap:18px;padding:0 22px;height:100px}
  .offer+.offer{border-left:2px solid var(--line)}
  .rival{width:110px;text-align:center;font-family:"Alfa Slab One",serif;font-size:20px;color:var(--ink);line-height:1.05}
  .rival-disc{width:110px;height:110px;border-radius:50%;background:var(--green);display:flex;align-items:center;justify-content:center;color:var(--white);font-family:"Alfa Slab One",serif;font-size:18px;text-align:center;line-height:1.05}
  .own-disc{background:var(--yellow);color:var(--green)}
  .prices{display:flex;flex-direction:column;gap:3px;font-size:12.5px;color:var(--ink)}
  .price{display:inline-block;background:var(--green);color:var(--white);font-family:"Alfa Slab One",serif;font-size:20px;padding:3px 12px;border:2px solid var(--green-dark);width:max-content}
  .price sup{font-size:10px}

  /* back */
  .back-shape{position:absolute;left:0;top:0}
  .back-head{position:absolute;left:42px;top:72px}
  .back-head .y{color:var(--yellow);font-size:36px}
  .back-head .w{color:var(--white);font-size:36px;margin-top:4px}
  .photo{position:absolute;border:4px solid var(--yellow);background:linear-gradient(160deg,#8d8a7e,#4f5a4a)}
  .photo.p1{left:42px;top:210px;width:148px;height:210px;transform:rotate(1.5deg)}
  .photo.p2{left:178px;top:196px;width:150px;height:210px;transform:rotate(-3deg);background:linear-gradient(160deg,#c9c5bb,#6e6a61)}
  .photo.p3{left:318px;top:204px;width:142px;height:220px;transform:rotate(2deg);background:linear-gradient(160deg,#a9b49a,#3e4a3a)}
  .truck-art{position:absolute;left:380px;top:370px;width:186px;height:236px;border-radius:14px;background:linear-gradient(170deg,#3f8a95 0%,#cfdede 55%,#ffffff 100%)}
  .call-tag{position:absolute;left:44px;top:500px;background:var(--green-mid);border:2px solid var(--yellow);color:var(--white);font-family:"Alfa Slab One",serif;font-size:13px;padding:4px 14px;transform:skewX(-12deg);white-space:nowrap}
  .back-phone{position:absolute;left:42px;top:534px;font-family:"Alfa Slab One",serif;font-size:40px;line-height:1;color:var(--yellow);white-space:nowrap}
  .back-web{position:absolute;left:46px;top:586px;font-family:"Alfa Slab One",serif;font-size:15px;line-height:1;color:var(--white);white-space:nowrap}
  .stamp{position:absolute;left:750px;top:36px;width:98px;height:98px;background:var(--stamp)}
  .address-line{position:absolute;left:586px;width:252px;height:2px;background:var(--line)}
</style>
</head>
<body>

<section class="leaflet front" aria-label="Leaflet front">
  <div class="front-green"></div>
  <div class="hero-art" role="img" aria-label="Illustration of a smiling mover in a yellow cap and shirt holding a fragile box, with the company removal truck behind him"></div>
  <div class="brand-badge"><span>STEADY<br>HAULERS</span></div>
  <h1 class="headline slab">
    <div class="y">Very Very</div>
    <div class="y">Very Cheap</div>
    <div class="w">Movers</div>
  </h1>
  <div class="phone-band">
    <span class="num">0400 123 987</span>
    <span class="sep"></span>
    <span class="web">WWW.STEADYHAULERS.COM.AU</span>
  </div>
  <div class="offers">
    <div class="offer">
      <div class="rival">DUO LIFT CO</div>
      <div class="prices">
        <span>1st Hour</span>
        <span class="price"><sup>$</sup>465</span>
        <span>Then Per Hour</span>
        <span class="price"><sup>$</sup>250</span>
      </div>
    </div>
    <div class="offer">
      <div class="rival-disc">VAN<br>FELLA</div>
      <div class="prices">
        <span class="price"><sup>$</sup>225</span>
        <span>Per Hour Base<br>to Base From<br>Elmridge</span>
      </div>
    </div>
    <div class="offer">
      <div class="rival-disc own-disc">STEADY<br>HAULERS</div>
      <div class="prices">
        <span class="price"><sup>$</sup>170</span>
        <span>Per Hour no<br>base to base<br>change</span>
      </div>
    </div>
  </div>
</section>

<section class="leaflet back" aria-label="Leaflet back">
  <svg class="back-shape" width="884" height="628" viewBox="0 0 884 628">
    <path d="M0 0 H318 C490 40 578 220 565 382 C558 480 538 560 512 628 H0 Z" fill="var(--yellow)"/>
    <path d="M0 0 H302 C470 40 560 220 547 382 C540 480 520 560 494 628 H0 Z" fill="var(--green)"/>
  </svg>
  <h2 class="back-head slab">
    <div class="y">Very Very Very</div>
    <div class="w">Cheap Movers</div>
  </h2>
  <div class="photo p1" role="img" aria-label="Photo of a mover loading a stone slab on a trolley into the truck"></div>
  <div class="photo p2" role="img" aria-label="Photo of movers carrying a bed frame inside an apartment"></div>
  <div class="photo p3" role="img" aria-label="Photo of a mover wheeling a strapped item on a hand truck"></div>
  <div class="truck-art" role="img" aria-label="Photo of the company removal truck"></div>
  <div class="call-tag">CALL DIRECT</div>
  <div class="back-phone">0400 123 987</div>
  <div class="back-web">WWW.STEADYHAULERS.COM.AU</div>
  <div class="stamp"></div>
  <div class="address-line" style="top:198px"></div>
  <div class="address-line" style="top:254px"></div>
  <div class="address-line" style="top:310px"></div>
</section>

</body>
</html>
```